Bramwell's Meadow Larder Limited (Uncoded design only)

To design a new modern website to replace an existing website.
www.clothdumplings.co.uk
we want to keep the same website address and pages - unless you hae new ideas for the pages.
We are initially looking for design only (no coding requirements)
We want wording 'Bramwell's Cloth Dumplings' to be used and Bramwell's Meadow Larder Limited to be the comapny address rather than what it is now.
I attach a new logo 'Bramwell lad' and new packaing design (Zip file). NOTE the blue man is to be replaced with the new 'Bramwells lad 'file i.e.the man with the union jack flag on his chest.
We would like coordination of the packing colourson the new website please.

Target Market(s)

Online sales to supermarkets

Industry/Entity Type

Food manufacturing

Coding

Coded - Design and coding required

Number of Pages Required

4 page

Font styles to use
Other font styles liked:
• Happy for any choice of font styles as I'm not stuck with the font of the packaging. I'm happy to go with what you feel looks the best and we can change the package to suit

Requirements
Must have
• Links to Facebook, Instagram and LinkedIn

```html
<!DOCTYPE html>
<html lang="en">
<head>
<meta charset="utf-8">
<title>Bramwell's Cloth Dumplings</title>
<link href="https://fonts.googleapis.com/css2?family=Montserrat:wght@500;600;700;800&family=Open+Sans:wght@400;600&family=Oswald:wght@600&display=swap" rel="stylesheet">
<style>
:root{
  --black:#000;
  --panel:#0e0e0e;
  --orange:#e0773f;
  --orange-deep:#c85a2c;
  --rust:#7d2c14;
  --white:#fff;
  --muted:#d8d8d8;
  --navy:#1c2a6b;
  --field-line:#3a3a3a;
  --pastry:#d9b77c;
  --pastry-dark:#a8773c;
  --gravy:#6b3d1c;
  --plate:#f1f0ec;
  --pea:#7fae3a;
  --custard:#f3dc6a;
}
*{margin:0;padding:0;box-sizing:border-box}
html,body{width:1200px;height:4491px;overflow:hidden;background:var(--black)}
body{position:relative;font-family:"Open Sans",Arial,sans-serif;color:var(--white)}
.heading{font-family:"Montserrat",Arial,sans-serif;font-weight:700;text-transform:uppercase;letter-spacing:.5px}
.btn{position:absolute;display:flex;align-items:center;justify-content:center;border-radius:40px;font-family:"Montserrat",Arial,sans-serif;font-weight:700;font-size:15px;text-transform:uppercase;color:var(--white);background:linear-gradient(90deg,var(--rust),var(--orange));letter-spacing:.3px}
.photo{position:absolute}

/* header */
.site-header{position:absolute;left:0;top:0;width:1200px;height:91px;background:var(--black);z-index:2}
.brand{position:absolute;left:122px;top:14px;width:204px;height:108px;background:var(--white);border-radius:18px;display:flex;align-items:center;justify-content:center;text-align:center;z-index:3;box-shadow:0 2px 6px rgba(0,0,0,.4)}
.brand span{font-family:"Montserrat",Arial,sans-serif;font-weight:700;font-size:17px;line-height:1.2;color:var(--navy);padding:0 12px}
.main-nav a{position:absolute;top:35px;font-size:15px;color:var(--white);text-decoration:none}
.cart{position:absolute;left:1008px;top:25px;width:40px;height:40px;border-radius:50%;background:var(--orange);display:flex;align-items:center;justify-content:center}
.cart-count{position:absolute;left:1034px;top:20px;width:16px;height:16px;border-radius:50%;background:var(--orange);font-size:10px;display:flex;align-items:center;justify-content:center}

/* hero */
.hero{position:absolute;left:0;top:91px;width:1200px;height:614px}
.hero-panel{position:absolute;left:0;top:0;width:581px;height:614px;background:linear-gradient(100deg,#7e3219 0%,#b5512a 55%,#d26a37 100%)}
.hero-photo{left:581px;top:0;width:619px;height:614px;
  background:radial-gradient(ellipse 330px 230px at 55% 46%,#e8c98a 0%,var(--pastry) 26%,var(--pastry-dark) 40%,#8fb04a 50%,var(--plate) 60%,#e2e2e2 78%,#6d6d70 86%,#2a2a2c 94%,#141414 100%)}
.hero h1{position:absolute;left:112px;top:182px;font-size:55px;line-height:58px;font-weight:700}
.hero p{position:absolute;left:112px;top:309px;font-family:"Montserrat",Arial,sans-serif;font-weight:600;font-size:19px;line-height:29px}
.hero .btn{left:112px;top:392px;width:164px;height:54px;background:var(--orange)}
.dots{position:absolute;left:572px;top:562px;display:flex;gap:4px}
.dots i{display:block;width:9px;height:9px;border-radius:50%;background:var(--white)}
.dots i.on{background:var(--orange)}

/* delivery */
.delivery{position:absolute;left:0;top:705px;width:1200px;height:650px;background:var(--black)}
.delivery-photo{left:106px;top:69px;width:450px;height:450px;border-radius:50%;border:7px solid var(--white);
  background:radial-gradient(circle at 52% 50%,#f2d79a 0%,#e2b568 24%,#c8903f 44%,#b9b9b6 58%,#dcdcda 66%,#b98a4e 74%,#d4a765 88%,#9c7040 100%)}
.delivery h2{position:absolute;left:586px;top:140px;font-size:35px;line-height:46px;width:540px}
.delivery p{position:absolute;left:586px;font-size:15px;line-height:26px;color:var(--muted);width:520px}
.delivery .btn{left:579px;top:380px;width:183px;height:61px}

/* methods */
.methods{position:absolute;left:0;top:1355px;width:1200px;height:795px;background:var(--panel)}
.methods h2{position:absolute;left:0;width:1200px;top:75px;text-align:center;font-size:35px}
.method-card{position:absolute;top:161px;width:320px;height:430px}
.method-card.oven{background:linear-gradient(180deg,#3f6a2a 0%,#c85f2a 20%,#d9b98a 38%,#c9a672 55%,#5a4a34 72%,#141210 86%,#080808 100%)}
.method-card.steam{background:linear-gradient(180deg,#4d8a2a 0%,#7fae3a 16%,#e5dccb 28%,#d6c29a 45%,#b99b6c 58%,#4a3d2c 74%,#121110 88%,#080808 100%)}
.method-card.micro{background:linear-gradient(180deg,#e9e8e4 0%,#d8c26a 16%,#c9a94f 28%,#d7bf92 45%,#a88a5e 60%,#3b3429 76%,#101010 90%,#080808 100%)}
.method-card span{position:absolute;left:0;width:100%;bottom:44px;text-align:center;font-family:"Montserrat",Arial,sans-serif;font-weight:700;font-size:26px;letter-spacing:.5px}
.methods .btn{left:495px;top:640px;width:183px;height:61px;font-family:"Oswald",Arial,sans-serif;font-weight:600;font-size:18px}

/* story band */
.story{position:absolute;left:0;top:2150px;width:1200px;height:339px;background:linear-gradient(90deg,#d8733a 0%,#c5602e 50%,#cf6d38 100%)}
.story p{position:absolute;left:95px;width:1010px;top:97px;text-align:center;font-size:23.5px;line-height:42px;font-weight:600;letter-spacing:.3px}

/* gallery */
.gallery{position:absolute;left:0;top:2489px;width:1200px;height:641px;background:var(--black)}
.gallery h2{position:absolute;left:0;width:1200px;top:82px;text-align:center;font-size:35px}
.slide-side{top:225px;width:96px;height:287px;border:4px solid var(--white)}
.slide-side.left{background:linear-gradient(180deg,#d7d3c6 0%,#bdb7a2 30%,#a98550 55%,#8a6a3c 75%,#e6e4de 100%)}
.slide-side.right{background:linear-gradient(180deg,#7a6c5a 0%,#c9bfae 30%,#e9ede9 50%,#8fc79a 62%,#f2f2f2 80%,#d9d9d9 100%)}
.slide-main{left:309px;top:185px;width:582px;height:366px;border:5px solid var(--white);border-radius:4px;
  background:linear-gradient(100deg,#1b1b1b 0%,#dcdcd8 8%,#f4f3ef 18%,#9a6a35 30%,#7c4f26 42%,var(--custard) 52%,#f6e48a 64%,#e9d35e 72%,#f2f1ec 84%,#d2d2ce 100%)}

/* contact */
.contact{position:absolute;left:0;top:3130px;width:1200px;height:750px;background:var(--panel)}
.contact h2{position:absolute;left:0;width:1200px;top:96px;text-align:center;font-size:35px}
.contact .intro{position:absolute;left:0;width:1200px;top:155px;text-align:center;font-size:14px}
.field{position:absolute;height:54px;width:389px;border:1px solid var(--field-line);padding:0 19px;display:flex;align-items:center;font-size:14px;color:var(--muted)}
.field.message{height:106px;width:790px;align-items:flex-start;padding-top:18px}
.contact .btn{left:504px;top:480px;width:194px;height:53px;background:linear-gradient(90deg,#6e2210,#a8401f)}

/* careers */
.careers{position:absolute;left:143px;top:3771px;width:914px;height:265px;background:linear-gradient(90deg,#e0824a,#d36e3a);border-radius:3px}
.careers p{position:absolute;left:0;width:914px;top:38px;text-align:center;font-size:23px;line-height:44px;font-weight:700;color:#fbe2d0}
.careers .btn{left:359px;top:188px;width:194px;height:53px;background:linear-gradient(90deg,#6e2210,#a8401f)}

/* footer */
.site-footer{position:absolute;left:0;top:3880px;width:1200px;height:611px;background:var(--black)}
.footer-brand{position:absolute;left:471px;top:215px;width:262px;height:134px;background:var(--white);border-radius:22px;display:flex;align-items:center;justify-content:center;text-align:center}
.footer-brand span{font-family:"Montserrat",Arial,sans-serif;font-weight:700;font-size:21px;line-height:1.25;color:var(--navy);padding:0 16px}
.footer-nav a{position:absolute;top:398px;font-size:15px;color:var(--white);text-decoration:none}
.copyright{position:absolute;left:0;width:1200px;top:455px;text-align:center;font-size:12.5px}
.copyright a{color:var(--orange)}
.social{position:absolute;top:506px;width:42px;height:42px;border-radius:50%;display:flex;align-items:center;justify-content:center;font-family:"Montserrat",Arial,sans-serif;font-weight:700;font-size:11px}
.social.primary{background:var(--orange);color:var(--white)}
.social.plain{background:var(--white);color:var(--rust)}
</style>
</head>
<body>

<header class="site-header">
  <nav class="main-nav">
    <a style="left:515px">Home</a>
    <a style="left:597px">Privacy Policy</a>
    <a style="left:736px">Contact</a>
    <a style="left:833px">Shop</a>
    <a style="left:912px">Delivery</a>
  </nav>
  <div class="cart" aria-label="Basket">
    <svg width="18" height="16" viewBox="0 0 18 16"><path d="M1 2h3l2 8h9l2-6H5" fill="none" stroke="#fff" stroke-width="2" stroke-linejoin="round"/><circle cx="7" cy="13.5" r="1.6" fill="#fff"/><circle cx="14" cy="13.5" r="1.6" fill="#fff"/></svg>
  </div>
  <div class="cart-count">0</div>
</header>
<div class="brand"><span>Bramwell's Cloth Dumplings</span></div>

<section class="hero">
  <div class="hero-panel"></div>
  <div class="photo hero-photo" role="img" aria-label="Plated cloth dumpling cut open with chips, mushy peas and a jug of gravy on a white plate"></div>
  <h1 class="heading">Handmade in<br>Lancashire</h1>
  <p>Local Apprentice Opportunity<br>apply here</p>
  <a class="btn">Buy Online</a>
  <div class="dots"><i></i><i></i><i class="on"></i><i></i><i></i></div>
</section>

<section class="delivery">
  <div class="photo delivery-photo" role="img" aria-label="Golden baked pie in a foil tray with a slice removed, on a wooden board"></div>
  <h2 class="heading">Local delivery only £1 in all ‘OL’ postcodes</h2>
  <p style="top:252px">Delivery charge will be applied automatically when you proceed to checkout as local postcode is recognised.</p>
  <p style="top:329px">There is also an option to collect from the factory shop</p>
  <a class="btn">Buy Online</a>
</section>

<section class="methods">
  <h2 class="heading">How do you like yours?</h2>
  <div class="method-card oven" style="left:108px" role="img" aria-label="Oven baked dumpling with salad and sweet potato fries"><span>OVEN BAKE</span></div>
  <div class="method-card steam" style="left:441px" role="img" aria-label="Steamed dumpling with peas and mash"><span>STEAM</span></div>
  <div class="method-card micro" style="left:774px" role="img" aria-label="Microwaved dumpling with new potatoes and asparagus"><span>MICROWAVE</span></div>
  <a class="btn">View All</a>
</section>

<section class="story" role="img" aria-label="Soft background of plated dumplings in orange tones">
  <p class="heading">Historically, the puddings take their name from the cloth they are wrapped in while they are steamed. Today, a hi-tech material is used instead of the original `rags’.</p>
</section>

<section class="gallery">
  <h2 class="heading">Sweet or Savoury</h2>
  <div class="photo slide-side left" style="left:218px" role="img" aria-label="Savoury dumpling with creamy sauce"></div>
  <div class="photo slide-side right" style="left:882px" role="img" aria-label="Boxed dumplings in retail packaging"></div>
  <div class="photo slide-main" role="img" aria-label="Sweet dumpling served with custard on a white plate"></div>
</section>

<section class="contact">
  <h2 class="heading">Contact Us</h2>
  <p class="intro">Please contact us via this form and we will get back to soon</p>
  <div class="field" style="left:204px;top:217px">Your Name (required)</div>
  <div class="field" style="left:605px;top:217px">Your Email (required)</div>
  <div class="field" style="left:204px;top:285px">Subject</div>
  <div class="field" style="left:605px;top:285px">Spam filter: What is the capital of England?</div>
  <div class="field message" style="left:204px;top:353px">Your Message</div>
  <a class="btn">Submit</a>
</section>

<footer class="site-footer">
  <div class="footer-brand"><span>Bramwell's Cloth Dumplings</span></div>
  <nav class="footer-nav">
    <a style="left:356px">Home</a>
    <a style="left:442px">Privacy Policy</a>
    <a style="left:588px">Contact</a>
    <a style="left:691px">Shop</a>
    <a style="left:775px">Delivery</a>
  </nav>
  <p class="copyright">Copyright© 2023 &nbsp;<a>Bramwell's Meadow Larder Limited</a> &nbsp;| &nbsp;All Rights Reserved</p>
  <a class="social primary" style="left:501px" aria-label="Facebook">FB</a>
  <a class="social plain" style="left:553px" aria-label="LinkedIn">LI</a>
  <a class="social plain" style="left:605px" aria-label="Instagram">IG</a>
</footer>

<section class="careers" role="img" aria-label="Warm orange backdrop of a plated dumpling">
  <p class="heading">Our purpose built facilities are dedicated to<br>providing consistantl &nbsp;perfectrag puddings to<br>customers worldwide</p>
  <a class="btn">Apply Here</a>
</section>

</body>
</html>
```